Ward Compass Business Card Design*

We need a business card design for our company Ward Compass. Our company is specialized in providing online consulting services regarding medical institutions, hospitals and doctors. We work with patients worldwide looking to choose between healthcare providers. We have a website you may use as a reference, where we list doctors and clinics worldwide. So we target Medical providers as well as patients worldwide.
Target Market(s)
Medical Providers and patients around the world
Industry/Entity Type
Medical
Contact Information for Business Card
Salwa Kettani
CEO
+90 612 348 2175
info@wardcompass.example
www.wardcompass.example
14 Annakhil 7 H.R.B. Rabat, Morocco
Requirements
Must have
- Company logo/name on one full side, personal info and smaller logo and company name on the other side.
Nice to have
- Smart and elegant design

```html
<!DOCTYPE html>
<html lang="en">
<head>
<meta charset="utf-8">
<title>Ward Compass — Business Card</title>
<link rel="stylesheet" href="https://fonts.googleapis.com/css2?family=Lato:wght@400;700&display=swap">
<style>
  :root {
    --backdrop: #2b2623;
    --card: #0e0e0e;
    --card-edge: #1c1c1c;
    --green: #9ccc2e;
    --yellow: #ece83a;
    --text: #cfcfcf;
    --muted: #9a9a9a;
    --divider: #2e2e2e;
  }
  * { box-sizing: border-box; margin: 0; padding: 0; }
  html, body {
    width: 1200px; height: 844px; overflow: hidden;
    background: var(--backdrop);
    font-family: "Lato", Arial, sans-serif;
  }
  .sheet {
    width: 1200px; height: 844px;
    display: flex; align-items: center; justify-content: center; gap: 60px;
  }
  .card {
    width: 525px; height: 300px;
    background: var(--card);
    border: 1px solid var(--card-edge);
    border-radius: 3px;
    box-shadow: 0 18px 40px rgba(0,0,0,.45);
    position: relative;
  }
  /* Personal side */
  .card--personal { display: flex; }
  .brand-panel {
    width: 44%;
    display: flex; align-items: center; justify-content: center;
    border-right: 1px solid var(--divider);
    margin: 40px 0;
  }
  .brand-name {
    color: var(--green);
    font-weight: 700;
    font-size: 22px;
    letter-spacing: .5px;
    text-transform: uppercase;
    display: flex; align-items: center; gap: 10px;
  }
  .brand-dot {
    width: 22px; height: 22px; border-radius: 50%;
    background: var(--yellow);
    flex: none;
  }
  .contact-panel {
    flex: 1;
    padding: 92px 0 0 34px;
  }
  .person-name {
    color: var(--green);
    font-weight: 700;
    font-size: 17px;
    text-transform: uppercase;
    letter-spacing: .3px;
  }
  .person-role {
    color: var(--text);
    font-size: 13px;
    margin-top: 2px;
  }
  .contact-list { list-style: none; margin-top: 26px; }
  .contact-list li {
    color: var(--text);
    font-size: 13px;
    line-height: 19px;
    display: flex; align-items: center; gap: 7px;
  }
  .contact-icon { width: 11px; height: 11px; flex: none; fill: var(--green); }
  /* Brand side */
  .card--brand {
    display: flex; align-items: center; justify-content: center;
  }
  .card--brand .brand-name { font-size: 30px; gap: 14px; }
  .card--brand .brand-dot { width: 44px; height: 44px; }
</style>
</head>
<body>
<main class="sheet">
  <section class="card card--personal" aria-label="Business card, personal side">
    <div class="brand-panel">
      <div class="brand-name"><span class="brand-dot"></span>Ward Compass</div>
    </div>
    <div class="contact-panel">
      <h1 class="person-name">Salwa Kettani</h1>
      <p class="person-role">CEO</p>
      <ul class="contact-list">
        <li>
          <svg class="contact-icon" viewBox="0 0 12 12" aria-hidden="true"><path d="M1 3.5c0-1 1-2 2.2-2h5.6C10 1.5 11 2.5 11 3.5L9 4.5 8 3H4L3 4.5zM3 5h6l1.5 5.5h-9z"/></svg>
          +90 612 348 2175
        </li>
        <li>
          <svg class="contact-icon" viewBox="0 0 12 12" aria-hidden="true"><path d="M0.5 2.5h11v7h-11z M1 3l5 3.6L11 3" stroke="#0e0e0e" stroke-width="0.9"/></svg>
          info@wardcompass.example
        </li>
        <li>
          <svg class="contact-icon" viewBox="0 0 12 12" aria-hidden="true"><circle cx="6" cy="6" r="5.5"/><path d="M6 .5v11M.5 6h11M3.3 1.5c1.8 2.8 1.8 6.2 0 9M8.7 1.5c-1.8 2.8-1.8 6.2 0 9" stroke="#0e0e0e" stroke-width="0.8" fill="none"/></svg>
          www.wardcompass.example
        </li>
      </ul>
    </div>
  </section>

  <section class="card card--brand" aria-label="Business card, brand side">
    <div class="brand-name"><span class="brand-dot"></span>Ward Compass</div>
  </section>
</main>
</body>
</html>
```